Lar Ventura Banners Ads

We need to create 4 animated banners ads in GIF (3 arts for each banner) to Lar Ventura Publiclik Display Campaign
Lar Ventura is an ecommerce in Brazil that sells high end home products.
It is a Branding Campaign, but we will add products images on it, so it has to be very sofisticated like the brand is.

We need 4 designs - 1 design for each size:

- Retângulo inline (300 X 250)
- Retângulo grande (336 x 280)
- Banner (468 x 60)
- Cabeçalho (728 x 90)

Please, find the briefing in pdf archive attached

Text we can work on th banners:

1 - Sofisticação com exclusividade para sua Casa!
2 - chique, exclusivo e encantador
3 - Encantador, sofisticado e exclusivo

The final image has to have Fontenelle´s Logo, Lar Ventura´s logo and a call to action:

Confira nossos produtos exclusivos!

_________________________________________________________________
UPDATE

Please, for the colors, take the ones from pdf; (use more collors chics, silver and white, but not only this colors);
Don't forget the CALL TO ACTION " Confira nossos Produtos Exclusivos!"

If you'd like to meet the brand and the target, here is the page on Facebook: https://www.rededeamigos.example/LarVenturaHomeVentura

But please, DO NOT COPY ANY OF THESE EXAMPLES ON THE PAGE.
We need something more executive.

Target Market(s)

Woman 30+
Trendy, modern, sofisticated, married or mum, cosmopolitan,
UPPERCLASS

Industry/Entity Type

Call

Font styles to use
Script
Other font styles liked:
• ColfaxTrial

Requirements
Must have
• Product images
Text
Product Image + Call to action on final layer with logos
As you will see the example in pdf archive attached
Nice to have
• frames
Should not have
• people
flowers
girlish drawing

```html
<!DOCTYPE html>
<html lang="pt-BR">
<head>
<meta charset="UTF-8">
<title>Lar Ventura — Banners Display</title>
<link rel="stylesheet" href="https://fonts.googleapis.com/css2?family=Kaushan+Script&family=Arimo:wght@700&display=swap">
<style>
  :root {
    --stage: #ece8e3;
    --white: #ffffff;
    --silver: #d3d3d1;
    --silver-dark: #c4c4c2;
    --brand-grey: #8d857a;
    --ink: #111111;
    --cta-red: #e00b0b;
    --pink-a: #e8c6c1;
    --pink-b: #cfa8a3;
    --towel-a: #b9c8dc;
    --towel-b: #6f6a66;
    --quilt-a: #7f93c6;
    --quilt-b: #55679e;
  }
  * { box-sizing: border-box; margin: 0; padding: 0; }
  html, body { width: 1200px; height: 900px; overflow: hidden; }
  body { background: var(--stage); position: relative; }

  .banner { position: absolute; background: var(--white); overflow: hidden; }
  .brand-name {
    position: absolute; font-family: "Arimo", sans-serif; font-weight: 700;
    color: var(--brand-grey); text-transform: uppercase; white-space: nowrap; letter-spacing: .02em;
  }
  .silver-panel { position: absolute; background: var(--silver); border-radius: 50%; }
  .product-photo { position: absolute; }
  .headline {
    position: absolute; font-family: "Kaushan Script", cursive; color: var(--ink);
    line-height: .9; text-align: center; white-space: nowrap;
  }
  .cta {
    position: absolute; font-family: "Arimo", sans-serif; font-weight: 700;
    color: var(--cta-red); line-height: 1; text-align: center; white-space: nowrap;
  }

  /* Cabeçalho 728x90 */
  .leaderboard { left: 250px; top: 103px; width: 728px; height: 90px; }
  .leaderboard .silver-panel { left: 190px; top: -120px; width: 900px; height: 330px; border-radius: 60px 0 0 60px / 165px 0 0 165px; }
  .leaderboard .brand-name { left: 8px; top: 32px; font-size: 24px; }
  .leaderboard .product-photo { left: 555px; top: 0; width: 173px; height: 90px;
    background: linear-gradient(160deg, var(--pink-b), var(--pink-a) 45%, #f1dad6); }
  .leaderboard .cta { left: 200px; top: 37px; width: 130px; font-size: 13px; }
  .leaderboard .headline { left: 325px; top: 10px; width: 170px; font-size: 22px; }

  /* Banner 468x60 */
  .full-banner { left: 380px; top: 271px; width: 468px; height: 60px; }
  .full-banner .silver-panel { left: 120px; top: -80px; width: 600px; height: 220px; border-radius: 40px 0 0 40px / 110px 0 0 110px; }
  .full-banner .brand-name { left: 5px; top: 22px; font-size: 16px; }
  .full-banner .product-photo { left: 300px; top: 0; width: 168px; height: 60px;
    background: linear-gradient(180deg, var(--towel-a), #e0c4c4 45%, #a9c6df 65%, var(--towel-b)); }
  .full-banner .cta { left: 126px; top: 26px; width: 88px; font-size: 9px; }
  .full-banner .headline { left: 208px; top: 8px; width: 110px; font-size: 15px; }

  /* Retângulo inline 300x250 */
  .inline-rect { left: 252px; top: 472px; width: 300px; height: 250px; }
  .inline-rect .silver-panel { left: -80px; top: 38px; width: 460px; height: 420px; }
  .inline-rect .brand-name { left: 0; top: 4px; width: 300px; text-align: center; font-size: 30px; }
  .inline-rect .product-photo { left: 0; top: 62px; width: 175px; height: 188px; border-radius: 0 60px 0 0;
    background: linear-gradient(150deg, var(--quilt-a), var(--quilt-b)); }
  .inline-rect .headline { left: 136px; top: 105px; width: 162px; font-size: 21px; }
  .inline-rect .cta { left: 60px; top: 199px; width: 190px; font-size: 14px; }

  /* Retângulo grande 336x280 */
  .large-rect { left: 642px; top: 457px; width: 336px; height: 280px; }
  .large-rect .silver-panel { left: -60px; top: 42px; width: 460px; height: 460px; }
  .large-rect .brand-name { left: 0; top: 4px; width: 336px; text-align: center; font-size: 33px; }
  .large-rect .product-photo { left: 178px; top: 92px; width: 158px; height: 188px;
    background: linear-gradient(180deg, var(--towel-a), #e3c9c9 35%, #a8c7e3 60%, var(--towel-b) 78%, #a88563); }
  .large-rect .headline { left: 22px; top: 80px; width: 175px; font-size: 24px; }
  .large-rect .cta { left: 14px; top: 245px; width: 206px; font-size: 15px; }
</style>
</head>
<body>

<section class="banner leaderboard" aria-label="Cabeçalho 728x90">
  <div class="silver-panel"></div>
  <div class="product-photo" role="img" aria-label="Jogo de lençóis rosa com bordado branco"></div>
  <span class="brand-name">Lar Ventura</span>
  <p class="cta">Confira nossos<br>ProdutosExclusivos!</p>
  <p class="headline">Sofisticação com<br>exclusividade<br>para sua Casa!</p>
</section>

<section class="banner full-banner" aria-label="Banner 468x60">
  <div class="silver-panel"></div>
  <div class="product-photo" role="img" aria-label="Toalhas dobradas coloridas sobre cadeira de madeira"></div>
  <span class="brand-name">Lar Ventura</span>
  <p class="cta">Confira nossos<br>ProdutosExclusivos!</p>
  <p class="headline">Sofisticação com<br>exclusividade<br>para sua Casa!</p>
</section>

<section class="banner inline-rect" aria-label="Retângulo inline 300x250">
  <div class="silver-panel"></div>
  <div class="product-photo" role="img" aria-label="Colcha matelassê azul enrolada"></div>
  <span class="brand-name">Lar Ventura</span>
  <p class="headline">Sofisticação com<br>exclusividade<br>para sua Casa!</p>
  <p class="cta">Confira nossos Produtos<br>Exclusivos!</p>
</section>

<section class="banner large-rect" aria-label="Retângulo grande 336x280">
  <div class="silver-panel"></div>
  <div class="product-photo" role="img" aria-label="Pilha de toalhas sobre cadeira de madeira"></div>
  <span class="brand-name">Lar Ventura</span>
  <p class="headline">Sofisticação com<br>exclusividade<br>para sua Casa!</p>
  <p class="cta">Confira nossos Produtos<br>Exclusivos!</p>
</section>

</body>
</html>
```